Web Developer Needs a Business Card Design

I need a personal business card design that represents me as a web developer for potential employers. I would like the background to be a dark color on the front for contrast with my logo and name. The back will have all my information along with a smaller version of the logo. I want something with a modern look and feel, not too conservative. This will be used for potential employers and freelance work.

Industry/Entity Type

Business

Contact Information for Business Card

Front should have my logo and name. The back should have all my personal information which would include: name: Tom Varulek, phone: 570-614-3098, email: tomvarulek@quillbox.net, website url: www.tomvarulek.net, logo, web developer.

Font styles to use
Sans Serif

Requirements
Must have
• Must include my logo. The color palette base color will be the logo color.

```html
<!DOCTYPE html>
<html lang="en">
<head>
<meta charset="utf-8">
<title>Tom Varulek – Business Cards</title>
<link rel="stylesheet" href="https://fonts.googleapis.com/css2?family=Open+Sans:wght@400;600;700&display=swap">
<style>
  :root {
    --teal: #5fc4b0;
    --teal-dark: #3fa893;
    --ink: #4a4a4a;
    --paper: #ffffff;
    --night: #1c1c1c;
    --night-top: #3a3a3a;
    --silver: #c9c9c9;
    --backdrop: #ecebe8;
  }
  * { box-sizing: border-box; margin: 0; padding: 0; }
  html, body { width: 1200px; height: 913px; overflow: hidden; }
  body {
    background: var(--backdrop);
    font-family: "Open Sans", Arial, sans-serif;
    position: relative;
  }
  .card {
    position: absolute;
    width: 560px;
    height: 320px;
    border-radius: 18px;
    overflow: hidden;
    box-shadow: 0 10px 30px rgba(0,0,0,.18);
  }
  .card-back { left: 90px; top: 120px; background: var(--paper); }
  .card-front {
    left: 550px; top: 470px;
    background: linear-gradient(160deg, var(--night-top) 0%, var(--night) 60%);
  }
  .swoosh { position: absolute; inset: 0; width: 100%; height: 100%; }

  /* back side */
  .brand-mark {
    position: absolute;
    display: flex; flex-direction: column; align-items: center; gap: 10px;
  }
  .brand-mark .dot {
    border-radius: 50%;
    background: var(--teal);
  }
  .brand-mark .brand-name {
    color: var(--teal);
    font-weight: 700;
    letter-spacing: 1px;
  }
  .card-back .brand-mark { left: 70px; top: 50px; }
  .card-back .brand-mark .dot { width: 130px; height: 130px; }
  .card-back .brand-mark .brand-name { font-size: 22px; }
  .divider {
    position: absolute; left: 280px; top: 40px;
    width: 1px; height: 130px;
    background: linear-gradient(var(--paper), #9a9a9a, var(--paper));
  }
  .contact { position: absolute; left: 300px; top: 48px; color: var(--ink); }
  .contact .name { font-size: 22px; font-weight: 700; letter-spacing: .5px; text-transform: uppercase; }
  .contact .role { font-size: 13px; font-weight: 600; color: var(--teal); letter-spacing: 1px; margin-bottom: 10px; }
  .contact ul { list-style: none; }
  .contact li { display: flex; align-items: center; gap: 8px; font-size: 14px; line-height: 22px; }
  .contact svg { width: 12px; height: 12px; fill: var(--teal); flex: none; }

  /* front side */
  .card-front .brand-mark { left: 50%; top: 34px; transform: translateX(-50%); }
  .card-front .brand-mark .dot { width: 84px; height: 84px; }
  .card-front .brand-mark .brand-name { font-size: 18px; }
  .headline { position: absolute; left: 0; right: 0; top: 162px; text-align: center; color: #f2f2f2; }
  .headline .name { font-size: 32px; font-weight: 400; letter-spacing: 2px; text-transform: uppercase; }
  .headline .role { font-size: 17px; margin-top: 6px; color: #e6e6e6; }
</style>
</head>
<body>

<section class="card card-back" aria-label="Card back with contact details">
  <svg class="swoosh" viewBox="0 0 560 320" preserveAspectRatio="none" aria-hidden="true">
    <path d="M0 320 L0 300 Q300 290 560 175 L560 320 Z" fill="var(--teal)"/>
    <path d="M150 300 Q380 270 560 168" fill="none" stroke="#6d6d6d" stroke-width="3"/>
  </svg>
  <div class="brand-mark">
    <span class="dot"></span>
    <span class="brand-name">VARULEK</span>
  </div>
  <span class="divider"></span>
  <div class="contact">
    <p class="name">Tom Varulek</p>
    <p class="role">WEB DEVELOPER</p>
    <ul>
      <li><svg viewBox="0 0 12 12"><path d="M2.5 0.5l2 2.5-1.2 1.3a7 7 0 0 0 4.4 4.4L9 7.5l2.5 2-1.3 2C5 11.5.5 7 .5 1.8z"/></svg>570-614-3098</li>
      <li><svg viewBox="0 0 12 12"><path d="M0 2h12v8H0zM1 3v.4l5 3.3 5-3.3V3zM1 4.6V9h10V4.6L6 8z"/></svg>tomvarulek@quillbox.net</li>
      <li><svg viewBox="0 0 12 12"><circle cx="6" cy="6" r="5.5"/></svg>www.tomvarulek.net</li>
    </ul>
  </div>
</section>

<section class="card card-front" aria-label="Card front with name">
  <svg class="swoosh" viewBox="0 0 560 320" preserveAspectRatio="none" aria-hidden="true">
    <path d="M0 320 L0 312 Q330 300 560 160 L560 320 Z" fill="var(--teal)"/>
    <path d="M230 300 Q420 260 560 152" fill="none" stroke="var(--silver)" stroke-width="4"/>
  </svg>
  <div class="brand-mark">
    <span class="dot"></span>
    <span class="brand-name">VARULEK</span>
  </div>
  <div class="headline">
    <p class="name">Tom Varulek</p>
    <p class="role">Front-End Developer</p>
  </div>
</section>

</body>
</html>
```